Moxy Fen needs some awesome stationary

Do you have what it takes to get my brand? You either do or you don't, have a crack at a design and you my just win my business.

I don't want to waste your or my time, so put your creative genius on either a business card or envelope.

I however need a package of stationary that follows the same brand. I will message you to complete the remaining should I like your first submission.

Here is what I need, have a go!

Basically I need the following for my small business based in melbourne.
- Letterhead (printer ready and MS Word)
- Business Card
- Compliments Slip
- Envelope
- Proposal Cover Page (MS Word only)
- Presentation Folder
- Marbled Fox Cards
- Student Name Tent
- Index Cards
- Vell-Ka

I am establishing the brand and it must be modern, professional but also relaxed; that is not formal and not corporate. It represents a company are leaders, but small enough to care and operate like a bunch of friends. We are bringing people and conversations back to business, and turfing out all the bureaucracy and crazy and wasteful procedures. Its about "lets talk and figure it out together and find even better ways".

Target Market(s)

Mainly companies that build software products, but Agile practices are used in many other industries (even graphic design projects)

Industry/Entity Type

Information Technology

Font styles to use
Sans Serif

Colors
3176b5
aaaaaa

Requirements
Must have
• I like curves and circles and not boxes or rectangles.
• I want a colour rich design with my brand colours, but it must be balanced.
• I want more modern than traditional, but simple modern
Should not have
• Not corporate
• Please don't waste my time if your not going to think about it.
• Don't mess with my primary logo
• Don't change my colours
• Don't overlay logo on image

```html
<!DOCTYPE html>
<html lang="en">
<head>
<meta charset="utf-8">
<title>Moxy Fen – Business Card</title>
<link href="https://fonts.googleapis.com/css2?family=Open+Sans:wght@400;600;700&display=swap" rel="stylesheet">
<style>
  :root {
    --brand-blue: #3176b5;
    --deep-blue: #2a5ea6;
    --brand-grey: #aaaaaa;
    --slate: #8e96a6;
    --ink: #555b66;
    --paper: #ffffff;
    --backdrop: #e9eaec;
  }
  * { margin: 0; padding: 0; box-sizing: border-box; }
  html, body { width: 1200px; height: 950px; overflow: hidden; }
  body {
    background: var(--backdrop);
    font-family: "Open Sans", sans-serif;
    position: relative;
  }
  .card {
    position: absolute;
    left: 320px;
    width: 560px;
    height: 320px;
    border-radius: 22px;
    overflow: hidden;
    box-shadow: 0 6px 18px rgba(0,0,0,.18);
  }
  .card-front { top: 110px; background: var(--paper); }
  .card-back { top: 520px; background: var(--deep-blue); }

  .front-curves { position: absolute; inset: 0; }

  .holder { position: absolute; right: 36px; top: 205px; text-align: right; }
  .holder-name { color: var(--deep-blue); font-weight: 700; font-size: 21px; }
  .holder-title { color: var(--slate); font-size: 13px; margin-top: 2px; }

  .brand { position: absolute; left: 36px; top: 92px; display: flex; align-items: center; gap: 12px; }
  .brand-dot { width: 54px; height: 54px; border-radius: 50%; background: var(--brand-blue); }
  .brand-name { color: var(--deep-blue); font-weight: 600; font-size: 30px; }

  .address { position: absolute; left: 38px; top: 170px; color: var(--ink); font-size: 12.5px; line-height: 17px; }
  .contacts { list-style: none; margin-top: 4px; }
  .contacts li { display: flex; align-items: center; gap: 7px; }
  .contacts svg { width: 11px; height: 11px; fill: var(--deep-blue); flex: none; }

  .back-web {
    position: absolute; left: 22px; top: 50%;
    transform: translate(-42%, -50%) rotate(90deg);
    color: #cdd8ec; font-size: 12px; letter-spacing: 3px;
  }
  .back-brand {
    position: absolute; inset: 0;
    display: flex; align-items: center; justify-content: center; gap: 16px;
  }
  .back-brand .brand-dot { width: 70px; height: 70px; background: var(--paper); }
  .back-brand .brand-name { color: var(--paper); font-size: 38px; }
</style>
</head>
<body>

<section class="card card-front">
  <svg class="front-curves" viewBox="0 0 560 320" preserveAspectRatio="none" aria-hidden="true">
    <path d="M250,0 H560 V150 C500,70 400,20 250,0 Z" fill="var(--deep-blue)"/>
    <path d="M290,4 C430,30 520,100 560,170 V205 C510,120 420,50 290,4 Z" fill="var(--brand-grey)"/>
  </svg>

  <div class="holder">
    <div class="holder-name">Dana Pellow</div>
    <div class="holder-title">CEO, Professional Scrum Trainer</div>
  </div>

  <div class="brand">
    <span class="brand-dot"></span>
    <span class="brand-name">Moxy Fen</span>
  </div>

  <div class="address">
    <p>PO Box 4410</p>
    <p>Kellbrook North</p>
    <p>VIC 3999, Australia</p>
    <ul class="contacts">
      <li><svg viewBox="0 0 12 12"><path d="M3 1 L5 3.5 L4 5 Q5.5 7 7 8 L8.5 7 L11 9 L9.5 11 Q4 10 1 3 Z"/></svg>1300 669 336</li>
      <li><svg viewBox="0 0 12 12"><rect x="3" y="0.5" width="6" height="11" rx="1"/></svg>+61 400 555 019</li>
      <li><svg viewBox="0 0 12 12"><path d="M0.5 2 H11.5 V10 H0.5 Z M1 2.5 L6 6.5 L11 2.5" stroke="#fff" stroke-width="0.8"/></svg>dana@moxy-fen.com.au</li>
      <li><svg viewBox="0 0 12 12"><circle cx="6" cy="6" r="5.5"/></svg>www.moxy-fen.com.au</li>
    </ul>
  </div>
</section>

<section class="card card-back">
  <div class="back-web">www.moxy-fen.com.au</div>
  <div class="back-brand">
    <span class="brand-dot"></span>
    <span class="brand-name">Moxy Fen</span>
  </div>
</section>

</body>
</html>
```